Car rental website design for a UAE car rental company

This project is about creating a new website design for a car rental company located in Dubai (United Arab Emirates), I opened the same project a few months ago but I didn't receive a lot of appealing entries so I closed it but this time I am marking the project as guaranteed to avoid such situation again, if you have already provided a design before then please re-submit again on this project so that it is considered while reviewing all the designs

A few important things:

1- We need a simple non-complex design
2- The final deliverable would be 2 screens (PSD, JPEG ... etc), the first screen is for the home page and the second screen is for an internal page
3- The home page must have a section that end users can use to rent a car online directly from the home page instead of going into some inner pages
4- The current website is very old and not very appealing so avoid creating a similar design (www.crestvane-autos.example)
5- The name is Crestvane but the company rents normal cars (no Limousin cars will be rented) so avoid adding any fancy cars in the images/graphics used in the design, just normal end users cars
6- The expected pages would be: home, About us, Our team, Strategy, Contact us and links to social media pages
7- The attachments include the company's logo and some screens from other car rental companies that provide online rentals/payments

If you have any questions please feel free to ask and please note that we will need the designs urgently

Thanks

Target Market(s)

Dubai - United Arab Emirates

Industry/Entity Type

It Company

Number of Pages Required

2 page

Font styles to use
Sans Serif

Requirements
Must have
• Check the project details
Nice to have
Should not have

```html
<!DOCTYPE html>
<html lang="en">
<head>
<meta charset="utf-8">
<title>Crestvane – Car Rental Dubai</title>
<link rel="stylesheet" href="https://fonts.googleapis.com/css2?family=Open+Sans:wght@400;600;700&family=Oswald:wght@500;600&display=swap">
<style>
:root{
  --brand:#a3163c;
  --brand-dark:#86102f;
  --ink:#333;
  --muted:#777;
  --line:#e4e4e4;
  --soft:#f6f6f6;
  --white:#fff;
}
*{box-sizing:border-box;margin:0;padding:0}
html,body{width:1200px;height:2192px;overflow:hidden}
body{position:relative;font-family:"Open Sans",Arial,sans-serif;color:var(--ink);background:var(--white)}
.abs{position:absolute}

/* header */
.site-header{position:absolute;left:0;top:0;width:1200px;height:170px;background:var(--soft)}
.brand{left:165px;top:14px;width:200px;height:150px;display:flex;flex-direction:column;align-items:center;gap:10px}
.brand-square{width:78px;height:78px;border:3px solid var(--brand);background:var(--white)}
.brand-name{font-size:30px;font-weight:600;color:#7b7f83;line-height:1}
.nav-rule{left:399px;top:109px;width:801px;height:1px;background:var(--line)}
.main-nav{left:399px;top:110px;height:60px;display:flex;font-size:18px;font-family:Arial,sans-serif}
.main-nav a{display:flex;align-items:center;padding:0 19px;color:#222;text-decoration:none;height:60px;white-space:nowrap}
.main-nav a.active{background:var(--brand);color:var(--white);padding:0 10px;margin-right:11px}
.lang{left:659px;top:41px;width:142px;height:38px;border:1px solid var(--line);background:var(--white);display:flex;align-items:center;padding-left:9px;font-size:13px;color:#333;font-family:Arial,sans-serif;gap:8px}
.flag{width:26px;height:16px;background:linear-gradient(#b22 0 15%,#fff 15% 30%,#b22 30% 45%,#fff 45% 60%,#b22 60% 75%,#fff 75% 90%,#b22 90%);position:relative}
.flag::before{content:"";position:absolute;left:0;top:0;width:12px;height:9px;background:#3b4b8c}
.phone-icon{left:830px;top:36px}
.contact-line{left:893px;top:34px;font-size:14px;color:#555;line-height:26px;font-family:Arial,sans-serif}

/* hero */
.hero{left:0;top:170px;width:1200px;height:520px;background:linear-gradient(100deg,#5e6b35 0%,#7d8a45 22%,#8d9378 42%,#6a6d6d 60%,#2b2b2c 80%,#191919 100%)}
.hero-copy{left:0;top:275px;width:1200px;text-align:center;color:var(--white);font-family:Oswald,sans-serif;text-transform:uppercase}
.hero-title{font-size:42px;line-height:58px;font-weight:500;letter-spacing:.5px}
.hero-sub{font-size:19px;margin-top:18px;font-weight:500}
.slider-arrow{top:412px;width:36px;height:36px;border-radius:50%;background:rgba(0,0,0,.55);display:flex;align-items:center;justify-content:center}
.btn{display:flex;align-items:center;justify-content:center;gap:22px;background:var(--brand);color:var(--white);font-size:17px;border-radius:3px;font-family:Arial,sans-serif}

/* welcome */
.welcome{left:0;top:690px;width:1200px;height:199px;background:var(--soft);border-bottom:1px solid var(--line)}
.section-title{width:1200px;text-align:center;font-size:23px;color:#333;text-transform:uppercase;font-weight:400}
.welcome h1{position:absolute;top:24px;width:1200px;text-align:center;font-size:29px;font-weight:400;color:#333}
.welcome p{position:absolute;left:170px;top:68px;width:860px;text-align:center;font-size:12px;line-height:20px;color:#666}

/* cards */
.car-card{top:984px;width:266px;height:337px;background:var(--white);border:1px solid #eee}
.car-photo{height:153px}
.car-label{height:41px;background:#f2f2f2;text-align:center;line-height:41px;font-size:16px;color:#555;position:relative}
.car-label::before{content:"";position:absolute;left:50%;top:-9px;margin-left:-10px;border:10px solid transparent;border-top:0;border-bottom:9px solid #f2f2f2}
.car-body{height:105px;text-align:center;padding-top:20px}
.price{color:var(--brand);font-size:16px;font-family:Arial,sans-serif}
.car-body p{font-size:11px;line-height:20px;color:#888;margin-top:7px;padding:0 20px}
.car-more{height:38px;background:#f7f7f7;display:flex;align-items:center;justify-content:center;gap:10px;color:var(--brand);font-size:13px;font-family:Arial,sans-serif}
.card-shadow{top:1322px;width:266px;height:20px;background:radial-gradient(ellipse at 50% 0,rgba(0,0,0,.28),rgba(0,0,0,0) 70%)}

/* finder */
.finder{left:0;top:1371px;width:1200px;height:257px;background:linear-gradient(180deg,#1b1b1d,#2c2c2e 60%,#3a3a3c)}
.finder h2{position:absolute;top:58px;width:1200px;text-align:center;color:var(--white);font-size:29px;font-weight:700;text-transform:uppercase}
.select{top:137px;height:41px;background:var(--white);font-size:12px;color:#444;display:flex;align-items:center;justify-content:space-between;padding:0 14px 0 17px;font-family:Arial,sans-serif}
.find-btn{left:839px;top:136px;width:196px;height:45px;border-radius:22px;background:var(--brand);color:var(--white);font-size:26px;font-weight:700;display:flex;align-items:center;justify-content:center;letter-spacing:1px;font-family:Arial,sans-serif}

/* blog */
.post{top:1711px;width:270px;height:226px;border:1px solid #e8e8e8;background:var(--white)}
.post-photo{position:absolute;left:17px;top:14px;width:237px;height:191px}
.date{position:absolute;left:176px;top:154px;width:62px;height:71px;background:var(--white);text-align:center}
.date b{display:block;font-size:30px;line-height:48px;color:#555;font-weight:700}
.date span{display:block;background:var(--brand);color:var(--white);font-size:9px;line-height:21px;font-weight:700}
.post-text{top:1947px;width:270px}
.post-text h3{font-size:14px;font-weight:400;color:#444;padding-left:18px}
.post-text p{font-size:11px;line-height:21px;color:#777;margin-top:10px;padding-left:18px}
.read{display:flex;align-items:center;gap:8px;font-size:10px;color:#555;margin-top:12px;padding-left:16px}
.dot{width:18px;height:18px;border-radius:50%;background:var(--brand-dark);display:flex;align-items:center;justify-content:center}

/* footer */
.site-footer{left:0;top:2083px;width:1200px;height:109px;background:var(--soft);border-top:1px solid var(--line)}
.copy{position:absolute;left:172px;top:29px;font-size:11px;color:#555}
.footer-links{position:absolute;left:170px;top:64px;font-size:14px;color:#222;font-family:Arial,sans-serif}
.news-title{position:absolute;left:754px;top:20px;font-size:15px;color:var(--brand)}
.news-input{position:absolute;left:754px;top:50px;width:186px;height:32px;background:var(--white);border:1px solid var(--line);font-size:10px;color:#888;padding-left:13px;line-height:30px}
.news-btn{position:absolute;left:951px;top:48px;width:79px;height:34px;background:var(--brand);color:var(--white);border-radius:3px;font-size:13px;display:flex;align-items:center;justify-content:center;font-family:Arial,sans-serif}
</style>
</head>
<body>

<header class="site-header">
  <div class="abs brand">
    <div class="brand-square"></div>
    <div class="brand-name">Crestvane</div>
  </div>
  <div class="abs lang">Languages <span class="flag"></span>
    <svg width="10" height="14" viewBox="0 0 10 14" style="margin-left:12px"><path d="M2 5l3-3 3 3M2 9l3 3 3-3" fill="none" stroke="#444" stroke-width="1.5"/></svg>
  </div>
  <svg class="abs phone-icon" width="40" height="40" viewBox="0 0 40 40">
    <circle cx="22" cy="18" r="13" fill="none" stroke="#888" stroke-width="2"/>
    <text x="22" y="22" font-size="11" text-anchor="middle" fill="#666" font-family="Arial">24</text>
    <path d="M4 22c2 8 8 14 15 16l3-4-4-3-3 2c-3-2-5-4-6-7l2-3-3-4z" fill="#888"/>
  </svg>
  <div class="abs contact-line">Questions? Call us<br>+971 4 000 0000</div>
  <div class="abs nav-rule"></div>
  <nav class="abs main-nav">
    <a class="active">Home</a><a>About us</a><a>Our team</a><a>Strategy</a><a>Vehicles</a><a>Contact us</a>
  </nav>
</header>

<section class="abs hero" role="img" aria-label="Close-up of a family car driving past a blurred green roadside"></section>
<div class="abs slider-arrow" style="left:57px"><svg width="12" height="14"><path d="M8 2L3 7l5 5" fill="none" stroke="#fff" stroke-width="2"/></svg></div>
<div class="abs slider-arrow" style="left:1110px"><svg width="12" height="14"><path d="M4 2l5 5-5 5" fill="none" stroke="#fff" stroke-width="2"/></svg></div>
<div class="abs hero-copy">
  <div class="hero-title">Hit the open road!<br>Comfortable everyday cars</div>
  <div class="hero-sub">At a truly affordable price!</div>
</div>
<svg class="abs" style="left:566px;top:459px" width="68" height="68" viewBox="0 0 68 68">
  <circle cx="34" cy="34" r="33" fill="rgba(255,255,255,.35)"/><path d="M27 21l21 13-21 13z" fill="rgba(255,255,255,.75)"/>
</svg>
<div class="abs btn" style="left:516px;top:551px;width:169px;height:41px">RENT A CAR
  <svg width="12" height="16"><path d="M2 2l7 6-7 6" fill="none" stroke="#fff" stroke-width="3"/></svg></div>

<section class="abs welcome">
  <h1>Welcome to Crestvane Car Rental</h1>
  <p>Crestvane is a Dubai car rental company offering compact cars, sedans and family SUVs for anyone who needs a car for business, holidays, airport transfers or daily city driving. We are unbeatable on service and very competitive on price, and every car you get from us is clean, insured and ready to go!</p>
  <div class="abs btn" style="left:516px;top:128px;width:169px;height:41px">Register Now
    <svg width="12" height="16"><path d="M2 2l7 6-7 6" fill="none" stroke="#fff" stroke-width="3"/></svg></div>
</section>

<h2 class="abs section-title" style="left:0;top:922px">Featured Cars</h2>

<article class="abs car-card" style="left:174px">
  <div class="car-photo" role="img" aria-label="Red car parked at sunset" style="background:linear-gradient(#9a6a3c,#5b3a2a 55%,#2d2a2a)"></div>
  <div class="car-label">Compact</div>
  <div class="car-body"><div class="price">From AED 120 per day</div><p>Lorem ipsum dolor sit amet, consectetur adipiscing elit, sed do eiusmod</p></div>
  <div class="car-more">Read More <svg width="12" height="10"><path d="M0 5h10M6 1l4 4-4 4" fill="none" stroke="#333" stroke-width="1.3"/></svg></div>
</article>
<div class="abs card-shadow" style="left:174px"></div>

<article class="abs car-card" style="left:469px">
  <div class="car-photo" role="img" aria-label="Red sedan driving on a blurred road" style="background:linear-gradient(135deg,#d9d9d9,#8b8b8b 50%,#b23a3a 75%,#555)"></div>
  <div class="car-label">Sedan</div>
  <div class="car-body"><div class="price">From AED 150 per day</div><p>Lorem ipsum dolor sit amet, consectetur adipiscing elit, sed do eiusmod</p></div>
  <div class="car-more">Read More <svg width="12" height="10"><path d="M0 5h10M6 1l4 4-4 4" fill="none" stroke="#333" stroke-width="1.3"/></svg></div>
</article>
<div class="abs card-shadow" style="left:469px"></div>

<article class="abs car-card" style="left:763px">
  <div class="car-photo" role="img" aria-label="Red car on a road under blue sky" style="background:linear-gradient(#6f8db8,#b8c6d6 50%,#6a6a6a)"></div>
  <div class="car-label">Family SUV</div>
  <div class="car-body"><div class="price">From AED 220 per day</div><p>Lorem ipsum dolor sit amet, consectetur adipiscing elit, sed do eiusmod</p></div>
  <div class="car-more">Read More <svg width="12" height="10"><path d="M0 5h10M6 1l4 4-4 4" fill="none" stroke="#333" stroke-width="1.3"/></svg></div>
</article>
<div class="abs card-shadow" style="left:763px"></div>

<section class="abs finder" role="img" aria-label="Dark parking garage background">
  <h2>Find a Rent Car</h2>
  <div class="abs select" style="left:172px;width:304px">Select a Make <svg width="10" height="8"><path d="M0 0h10L5 7z" fill="#777"/></svg></div>
  <div class="abs select" style="left:498px;width:329px">Select Car Model <svg width="10" height="8"><path d="M0 0h10L5 7z" fill="#777"/></svg></div>
  <div class="abs find-btn">FIND IT</div>
</section>

<h2 class="abs section-title" style="left:0;top:1658px">Blog Post</h2>

<article class="abs post" style="left:172px">
  <div class="post-photo" role="img" aria-label="Red car on an open road" style="background:linear-gradient(#6f8db8,#c0ccd8 50%,#666)"></div>
  <div class="date"><b>23</b><span>OCTOBER</span></div>
</article>
<article class="abs post" style="left:468px">
  <div class="post-photo" role="img" aria-label="Red sedan parked under evening sky" style="background:linear-gradient(#9aa3b8,#c8c0c0 55%,#8a8a8a)"></div>
  <div class="date"><b>23</b><span>OCTOBER</span></div>
</article>
<article class="abs post" style="left:760px">
  <div class="post-photo" role="img" aria-label="Red SUV in front of green trees" style="background:linear-gradient(#4f6a2e,#7e9444 45%,#8e2a2a 75%,#555)"></div>
  <div class="date"><b>23</b><span>OCTOBER</span></div>
</article>

<div class="abs post-text" style="left:172px"><h3>Phasellus commodo</h3><p>Sed ut perspiciatis unde omnis iste natus<br>error sit voluptatem accusantium doloremque</p><div class="read"><span class="dot"><svg width="6" height="8"><path d="M1 1l4 3-4 3" fill="none" stroke="#fff" stroke-width="1.5"/></svg></span>Read Article</div></div>
<div class="abs post-text" style="left:468px"><h3>Phasellus commodo</h3><p>Sed ut perspiciatis unde omnis iste natus<br>error sit voluptatem accusantium doloremque</p><div class="read"><span class="dot"><svg width="6" height="8"><path d="M1 1l4 3-4 3" fill="none" stroke="#fff" stroke-width="1.5"/></svg></span>Read Article</div></div>
<div class="abs post-text" style="left:760px"><h3>Phasellus commodo</h3><p>Sed ut perspiciatis unde omnis iste natus<br>error sit voluptatem accusantium doloremque</p><div class="read"><span class="dot"><svg width="6" height="8"><path d="M1 1l4 3-4 3" fill="none" stroke="#fff" stroke-width="1.5"/></svg></span>Read Article</div></div>

<footer class="abs site-footer">
  <div class="copy">©2014 Crestvane Car Rental, All Rights Reserved.</div>
  <div class="footer-links">Home | About us | Our team | Strategy | Vehicles | Contact us</div>
  <div class="news-title">Newsletter Sign Up</div>
  <div class="news-input">Enter Your Email</div>
  <div class="news-btn">Subscribe</div>
</footer>

</body>
</html>
```